business card, stationary, return address labels

acupuncture practice in private setting...www.needlecalmstudio.example.Hope for improvement in card design, especially background and arrangement of logo.Thank you,Patricia Heraghty203.297.5399

Business

Please see attached business card

```html
<!DOCTYPE html>
<html lang="en">
<head>
<meta charset="utf-8">
<title>Needle Calm Studio – Business Card</title>
<link href="https://fonts.googleapis.com/css2?family=Oswald:wght@500;700&family=Lato:wght@400&display=swap" rel="stylesheet">
<style>
  :root {
    --maroon: #560021;
    --white: #ffffff;
    --ink: #111111;
    --backdrop: #efece8;
    --shadow: rgba(0, 0, 0, 0.22);
  }
  * { margin: 0; padding: 0; box-sizing: border-box; }
  html, body { width: 1200px; height: 676px; overflow: hidden; }
  body { background: var(--backdrop); position: relative; }

  .card {
    position: absolute;
    left: 385px;
    width: 435px;
    height: 242px;
    overflow: hidden;
    box-shadow: 0 10px 18px var(--shadow);
  }
  .card--front { top: 68px; background: var(--white); }
  .card--back { top: 373px; background: var(--maroon); }

  .front-sweep { position: absolute; inset: 0; width: 435px; height: 242px; }

  .brand-name {
    position: absolute;
    font-family: "Oswald", sans-serif;
    font-weight: 700;
    line-height: 0.92;
    letter-spacing: -0.5px;
  }
  .card--front .brand-name {
    left: 18px; top: 36px;
    font-size: 31px;
    color: var(--ink);
  }
  .card--back .brand-name {
    left: 0; right: 0; top: 82px;
    text-align: center;
    font-size: 48px;
    color: var(--white);
  }

  .practitioner {
    position: absolute;
    left: 9px; top: 112px;
    font-family: "Oswald", sans-serif;
    font-weight: 500;
    font-size: 20px;
    letter-spacing: -0.6px;
    color: var(--ink);
    white-space: nowrap;
  }

  .contact {
    position: absolute;
    left: 255px; top: 142px;
    font-family: "Lato", sans-serif;
    font-size: 8.4px;
    color: var(--white);
    list-style: none;
  }
  .contact__item { display: flex; align-items: center; gap: 10px; margin-bottom: 6px; }
  .contact__icon { width: 16px; height: 16px; flex: none; }
  .contact__text { line-height: 12px; white-space: nowrap; }
</style>
</head>
<body>

  <section class="card card--front" aria-label="Business card front">
    <svg class="front-sweep" viewBox="0 0 435 242" aria-hidden="true">
      <path d="M340 0 H435 V242 H77 C210 205 310 135 340 0 Z" fill="var(--maroon)"/>
    </svg>

    <div class="brand-name">Needle Calm<br>Studio</div>
    <div class="practitioner">Lorraine Vasquell, LAc., Dipl.Ac., O.T.</div>

    <ul class="contact">
      <li class="contact__item">
        <svg class="contact__icon" viewBox="0 0 16 16" aria-hidden="true">
          <path d="M8 1.5a4.5 4.5 0 0 0-4.5 4.5C3.5 9.5 8 14.5 8 14.5S12.5 9.5 12.5 6A4.5 4.5 0 0 0 8 1.5Z" fill="var(--white)"/>
          <circle cx="8" cy="6" r="1.8" fill="var(--maroon)"/>
        </svg>
        <span class="contact__text">48B Orchard Hill Road<br>Westbrook, CT 06498<br>415.682.7013</span>
      </li>
      <li class="contact__item">
        <svg class="contact__icon" viewBox="0 0 16 16" aria-hidden="true">
          <rect x="1.5" y="3.5" width="13" height="9" fill="none" stroke="var(--white)" stroke-width="1.3"/>
          <path d="M1.5 3.5 8 9l6.5-5.5M1.5 12.5 6.2 7.6M14.5 12.5 9.8 7.6" fill="none" stroke="var(--white)" stroke-width="1.1"/>
        </svg>
        <span class="contact__text">lorraine@needlecalmstudio.example</span>
      </li>
      <li class="contact__item">
        <svg class="contact__icon" viewBox="0 0 16 16" aria-hidden="true">
          <path d="M1.5 6.5a9 9 0 0 1 13 0M3.8 8.8a5.8 5.8 0 0 1 8.4 0M6 11a2.8 2.8 0 0 1 4 0" fill="none" stroke="var(--white)" stroke-width="1.4" stroke-linecap="round"/>
          <circle cx="8" cy="13.2" r="1.1" fill="var(--white)"/>
        </svg>
        <span class="contact__text">www.needlecalmstudio.example</span>
      </li>
    </ul>
  </section>

  <section class="card card--back" aria-label="Business card back">
    <div class="brand-name">Needle Calm<br>Studio</div>
  </section>

</body>
</html>
```